New letter head for Air Conditioning business

We need a new professional letter head design to suit our new re-branded air conditioning business. Our new logo is attached

```html
<!DOCTYPE html>
<html lang="en">
<head>
<meta charset="utf-8">
<title>Norvane Letterhead</title>
<link rel="stylesheet" href="https://fonts.googleapis.com/css2?family=Open+Sans:wght@400;600;700&family=Dancing+Script:wght@500&display=swap">
<style>
  :root {
    --backdrop: #ececec;
    --paper: #ffffff;
    --coral: #ee6a5e;
    --green: #3fb67a;
    --ink: #3a3a3a;
    --ink-soft: #5a5a5a;
    --signature: #1f4e8c;
    --rule: #d6d6d6;
  }
  * { box-sizing: border-box; margin: 0; padding: 0; }
  html, body { width: 1200px; height: 795px; overflow: hidden; }
  body {
    background: var(--backdrop);
    font-family: "Open Sans", Arial, sans-serif;
    color: var(--ink);
  }
  .letterhead {
    position: absolute;
    left: 330px; top: 16px;
    width: 540px; height: 763px;
    background: var(--paper);
    box-shadow: 0 2px 10px rgba(0,0,0,0.12);
    overflow: hidden;
  }
  .header-band { position: absolute; top: 0; left: 0; width: 540px; height: 140px; }
  .contact-list {
    position: absolute; top: 16px; left: 330px;
    list-style: none; font-size: 8px; line-height: 12px; color: #fff;
  }
  .contact-list li { display: flex; align-items: center; gap: 5px; }
  .contact-icon {
    width: 8px; height: 8px; border-radius: 50%;
    background: var(--green); display: inline-block;
  }
  .brand {
    position: absolute; top: 140px; left: 40px;
    display: flex; align-items: center; gap: 8px;
  }
  .brand-dot { width: 14px; height: 14px; border-radius: 50%; background: var(--coral); }
  .brand-name { font-size: 24px; font-weight: 600; letter-spacing: 2px; color: var(--ink); line-height: 30px; }
  .brand-tagline {
    position: absolute; top: 171px; left: 62px;
    font-size: 7px; color: var(--green); letter-spacing: 0.5px;
  }
  .letter-body {
    position: absolute; top: 212px; left: 40px; width: 455px;
    font-size: 9px; line-height: 13px; color: var(--ink-soft);
  }
  .date, .recipient { font-size: 10px; color: var(--ink); font-weight: 600; line-height: 14px; }
  .recipient { margin-top: 12px; }
  .salutation { margin-top: 14px; font-size: 10px; font-weight: 700; color: var(--ink); }
  .letter-body p.para { margin-top: 14px; }
  .closing { margin-top: 20px; font-size: 9.5px; color: var(--ink); }
  .signature {
    font-family: "Dancing Script", cursive;
    font-size: 26px; line-height: 32px; color: var(--signature); margin: 4px 0 4px;
  }
  .signer { font-size: 9.5px; color: var(--ink); line-height: 13px; }
  .footer-rule {
    position: absolute; left: 40px; right: 40px; top: 665px;
    border-top: 1px solid var(--rule);
  }
  .footer {
    position: absolute; right: 40px; top: 680px; text-align: right;
    font-size: 8px; line-height: 11px;
  }
  .footer-brand { color: var(--coral); font-weight: 700; }
  .footer-tag { color: var(--green); }
  .footer-address { color: var(--ink); font-weight: 700; }
</style>
</head>
<body>
  <main class="letterhead">
    <svg class="header-band" viewBox="0 0 540 140" aria-hidden="true">
      <path d="M260 0 H540 V86 C460 80 390 88 320 108 C270 122 220 128 170 130 C210 90 240 40 260 0 Z" fill="var(--coral)"/>
      <path d="M170 135 C220 133 275 125 325 113 C395 95 465 87 540 93" fill="none" stroke="var(--green)" stroke-width="2.2"/>
    </svg>
    <ul class="contact-list">
      <li><span class="contact-icon"></span>(555) 014-2280</li>
      <li><span class="contact-icon"></span>(555) 014-2291</li>
      <li><span class="contact-icon"></span>info@norvaneair.com</li>
      <li><span class="contact-icon"></span>www.norvaneair.com</li>
    </ul>

    <div class="brand">
      <span class="brand-dot"></span>
      <span class="brand-name">NORVANE</span>
    </div>
    <div class="brand-tagline">Air Conditioning &amp; Refrigeration</div>

    <section class="letter-body">
      <p class="date">January 12, 2014</p>
      <p class="recipient">Mr. John Doe<br>President<br>AA Corporation<br>111 Street Name, Suite#<br>City, State, 12345</p>
      <p class="salutation">Dear Mr. John,</p>
      <p class="para">Lorem Ipsum is simply dummy text of the printing and typesetting industry. Lorem Ipsum has been the industry's standard dummy text ever since the 1500s, when an unknown printer took a galley of type and scrambled it to make a type specimen book. It has survived not only five centuries, but also the leap into electronic typesetting, remaining essentially unchanged.</p>
      <p class="para">The standard chunk of Lorem Ipsum used since the 1500s is reproduced below for those interested. Sections 1.10.32 and 1.10.33 from "de Finibus Bonorum et Malorum" by Cicero are also reproduced in their exact original form, accompanied by English versions from the 1914 translation by H. Rackham.</p>
      <p class="para">Lorem Ipsum is simply dummy text of the printing and typesetting industry. Lorem Ipsum has been the industry's standard dummy text ever since the 1500s, when an unknown printer took a galley of type and scrambled it to make a type specimen book. It has survived not only five centuries, but also the leap into electronic typesetting, remaining essentially unchanged. It was popularised in the</p>
      <p class="closing">Sincerely Your,</p>
      <p class="signature">your name</p>
      <p class="signer">Name Last Name<br>Company Name</p>
    </section>

    <div class="footer-rule"></div>
    <footer class="footer">
      <p class="footer-brand">NORVANE</p>
      <p class="footer-tag">Air Conditioning &amp; Refrigeration</p>
      <p class="footer-address">SUITE 102 STREET NAME, STATE, ZIP 2034, COUNTRY</p>
    </footer>
  </main>
</body>
</html>
```